Electrician Letterhead Design MVR

We need some letterhead for our bills and other papers.
Customer address is on the right side (Swiss format)
A4 format

Design should also be applicable on Cards

Target Market(s)

Private Customers, Small Business

Industry/Entity Type

Electrician

Other font styles liked:
• incised 901

Colors
00AB8E
00BBA5
67D7C9
C6EFE9
E9F9F6

```html
<!DOCTYPE html>
<html lang="en">
<head>
<meta charset="utf-8">
<title>MVR Letterhead</title>
<link href="https://fonts.googleapis.com/css2?family=Lato:wght@400;700&family=Montserrat:wght@400;500;700&family=Parisienne&display=swap" rel="stylesheet">
<style>
  :root {
    --teal: #019c8a;
    --teal-bright: #00ab8e;
    --teal-soft: #76c1b8;
    --ink: #333333;
    --ink-dark: #1c1c1c;
    --page: #f7f7f7;
    --backdrop: #e2e2e2;
  }
  * { margin: 0; padding: 0; box-sizing: border-box; }
  html, body { width: 1153px; height: 1200px; overflow: hidden; }
  body { background: var(--backdrop); position: relative; font-family: "Lato", sans-serif; color: var(--ink); }

  .letterhead {
    position: absolute; left: 169px; top: 30px;
    width: 815px; height: 1140px;
    background: radial-gradient(circle at 55% 38%, #ffffff 0%, var(--page) 60%, #f0f0f0 100%);
    overflow: hidden;
  }

  .brand { position: absolute; left: 61px; top: 56px; display: flex; align-items: center; gap: 12px; }
  .brand-name {
    font-family: "Montserrat", sans-serif; font-weight: 700;
    font-size: 82px; line-height: 1; color: var(--teal); letter-spacing: -1px;
  }
  .brand-dot { width: 22px; height: 22px; background: var(--teal); }

  .contact {
    position: absolute; left: 555px; top: 50px;
    border-left: 1.5px solid var(--teal);
    padding-left: 11px;
    font-family: "Montserrat", sans-serif; font-style: normal;
    font-size: 13.5px; color: var(--ink-dark); line-height: 18px;
  }
  .contact-address { margin-bottom: 7px; }
  .contact-line { display: flex; align-items: center; gap: 7px; line-height: 19px; }
  .contact-line svg { width: 12px; height: 12px; fill: var(--teal); flex: none; }

  .header-rule { position: absolute; left: 60px; top: 171px; width: 692px; height: 2px; background: var(--teal); }

  .letter { position: absolute; left: 63px; top: 250px; width: 689px; font-size: 15.5px; line-height: 18.5px; }

  .letter-top { display: flex; justify-content: space-between; align-items: flex-start; }
  .letter-date { font-size: 16px; }
  .recipient-block { width: 250px; margin-right: 0; }
  .recipient { margin-bottom: 18px; }
  .recipient:last-child { margin-bottom: 0; }

  .salutation { font-size: 19px; font-weight: 700; margin: 30px 0 18px; }
  .letter-body p { font-size: 15.2px; line-height: 17.5px; text-align: justify; margin-bottom: 17px; }
  .closing { margin-top: 39px; font-size: 15px; }
  .signature { font-family: "Parisienne", cursive; font-size: 38px; color: var(--ink-dark); margin-top: 20px; }

  .footer-band { position: absolute; left: 0; bottom: 0; width: 815px; height: 51px; display: block; }
</style>
</head>
<body>
  <main class="letterhead">
    <div class="brand">
      <span class="brand-name">MVR</span>
      <span class="brand-dot"></span>
    </div>

    <address class="contact">
      <div class="contact-address">42 Linden Street 7,<br>Fairview, NY 10987</div>
      <div class="contact-line">
        <svg viewBox="0 0 24 24"><path d="M6.6 10.8a15.1 15.1 0 0 0 6.6 6.6l2.2-2.2a1 1 0 0 1 1-.25 11.4 11.4 0 0 0 3.6.57 1 1 0 0 1 1 1V20a1 1 0 0 1-1 1A17 17 0 0 1 3 4a1 1 0 0 1 1-1h3.5a1 1 0 0 1 1 1c0 1.25.2 2.45.57 3.57a1 1 0 0 1-.25 1z"/></svg>
        <span>555-210-3486</span>
      </div>
      <div class="contact-line">
        <svg viewBox="0 0 24 24"><path d="M2 5h20v14H2z M2 5l10 8 10-8" fill="none" stroke="#019c8a" stroke-width="2.5"/></svg>
        <span>office@mvr-electric.com</span>
      </div>
      <div class="contact-line">
        <svg viewBox="0 0 24 24"><circle cx="12" cy="12" r="10"/></svg>
        <span>www.mvr-electric.com</span>
      </div>
    </address>

    <div class="header-rule"></div>

    <article class="letter">
      <div class="letter-top">
        <p class="letter-date">Feb-03-2022</p>
        <div class="recipient-block">
          <p class="recipient">Mr, James Carter<br>President</p>
          <p class="recipient">Harbor Corporation<br>123 Street Name, Suite# 10<br>City, State, 120023</p>
        </div>
      </div>
      <h2 class="salutation">Dear Mr, James</h2>
      <div class="letter-body">
        <p>Lorem ipsum dolor sit amet, consectetur adipisicing elit, sed do eiusmod tempor incididunt ut labore et dolore magna aliqua. Ut enim ad minim veniam, quis nostrud exercitation ullamco laboris nisi ut aliquip ex ea commodo consequat. Duis aute irure dolor in reprehenderit in voluptate velit esse cillum dolore eu fugiat nulla pariatur.</p>
        <p>Lorem ipsum dolor sit amet, consectetur adipisicing elit, sed do eiusmod tempor incididunt ut labore et dolore magna aliqua. Ut enim ad minim veniam, quis nostrud exercitation ullamco laboris nisi ut aliquip ex ea commodo consequat. Duis aute irure dolor in reprehenderit in voluptate velit esse cillum dolore eu fugiat nulla pariatur.</p>
        <p>Lorem ipsum dolor sit amet, consectetur adipisicing elit, sed do eiusmod tempor incididunt ut labore et dolore magna aliqua. Ut enim ad minim veniam, quis nostrud exercitation ullamco laboris nisi ut aliquip ex ea commodo consequat.</p>
        <p>Excepteur sint occaecat cupidatat non proident, sunt in culpa qui officia deserunt mollit anim id est laborum. re et dolore magnam aliquam quaerat voluptatem.</p>
      </div>
      <p class="closing">Regards</p>
      <p class="signature">Daniel Brooks</p>
    </article>

    <svg class="footer-band" viewBox="0 0 815 51" preserveAspectRatio="none" aria-hidden="true">
      <rect x="0" y="18" width="560" height="11" fill="var(--teal)"/>
      <polygon points="0,29 480,29 502,51 0,51" fill="var(--teal-soft)"/>
      <polygon points="480,29 548,29 527,51 502,51" fill="var(--teal-bright)"/>
      <polygon points="574,0 815,0 815,51 526,51 557,18" fill="var(--teal)"/>
    </svg>
  </main>
</body>
</html>
```